Local Flower Farm Needs Business Card Design

I need business cards designed for a flower farm based in Eudora, Kansas.
Business Info:
We are a local cut flower farm located in Eudora, Kansas, founded by Corinne Haldwick. What started as a passion for agriculture and search for more joy in daily life has blossomed into a small business dedicated to providing the community with beautiful, fresh, and sustainable flowers. We specialize in local, seasonal blooms, ensuring that every petal reflects the care and dedication we pour into our craft. Our mission is to deliver the highest quality flowers directly to our customers through local farmers markets and to florists who share our commitment to sustainability. Join us in celebrating the beauty of nature, one bloom at a time!
Contact Details:
Corinne Haldwick
Owner
Phone 913-555-0147
Facebook: Rosalind Thorpe Gardens
Instagram: @RosalindThorpeGardens
Website: RosalindThorpeGardens.example
Target Market(s)
Wholesale to Florists and Direct to Consumer via Farmers Market
Industry/Entity Type
Florist, Farm
Contact Information for Business Card
Name, Contact Info, Logo
Look and feel
Each slider illustrates characteristics of the customer's brand and the style your logo design should communicate.

```html
<!DOCTYPE html>
<html lang="en">
<head>
<meta charset="utf-8">
<title>Rosalind Thorpe Gardens — Business Card</title>
<link href="https://fonts.googleapis.com/css2?family=Montserrat:wght@400;500;700&display=swap" rel="stylesheet">
<style>
  :root {
    --backdrop: #e8e3da;
    --card-white: #ffffff;
    --deep-teal: #0a292d;
    --ink: #0d2528;
    --text: #1b1b1b;
    --faint: #e2e2e2;
    --line-white: #e9efee;
  }
  * { margin: 0; padding: 0; box-sizing: border-box; }
  html, body { width: 900px; height: 1200px; overflow: hidden; }
  body {
    background: var(--backdrop);
    font-family: "Montserrat", Arial, sans-serif;
    position: relative;
  }
  .card {
    position: absolute;
    width: 742px;
    height: 440px;
    border-radius: 22px;
    overflow: hidden;
  }
  .card-front { left: 80px; top: 131px; background: var(--card-white); }
  .card-back { left: 79px; top: 638px; background: var(--deep-teal); }

  .brand-badge {
    position: absolute;
    left: 35px; top: 39px;
    width: 156px; height: 156px;
    border: 1.5px solid var(--ink);
    border-radius: 50%;
    display: flex; align-items: center; justify-content: center;
    text-align: center;
    color: var(--ink);
    font-weight: 500;
    font-size: 15px;
    line-height: 1.35;
    letter-spacing: 0.08em;
    text-transform: uppercase;
  }
  .brand-watermark {
    position: absolute;
    left: 385px; top: 40px;
    width: 320px;
    color: var(--faint);
    font-weight: 700;
    font-size: 64px;
    line-height: 1.08;
    text-transform: uppercase;
  }
  .holder-name {
    position: absolute; left: 36px; top: 238px;
    font-weight: 700; font-size: 25px; color: var(--ink);
  }
  .holder-role {
    position: absolute; left: 36px; top: 272px;
    font-size: 15px; color: var(--text);
  }
  .contact-list {
    position: absolute; left: 36px; top: 306px;
    list-style: none;
  }
  .contact-list li {
    display: flex; align-items: center;
    height: 26px;
    font-size: 15.5px; color: var(--text);
  }
  .contact-icon { width: 15px; height: 15px; margin-right: 10px; flex: none; }

  .back-ring {
    position: absolute;
    left: 216px; top: 65px;
    width: 310px; height: 310px;
    border: 1.2px solid var(--line-white);
    border-radius: 50%;
    display: flex; align-items: center; justify-content: center;
    text-align: center;
    color: var(--card-white);
    font-weight: 500;
    font-size: 28px;
    line-height: 1.35;
    letter-spacing: 0.1em;
    text-transform: uppercase;
  }
</style>
</head>
<body>
  <section class="card card-front">
    <div class="brand-badge">Rosalind<br>Thorpe<br>Gardens</div>
    <div class="brand-watermark" aria-hidden="true">Rosalind Thorpe Gardens</div>

    <h1 class="holder-name">Corinne Haldwick</h1>
    <p class="holder-role">Owner</p>

    <ul class="contact-list">
      <li>
        <svg class="contact-icon" viewBox="0 0 24 24" aria-hidden="true">
          <path d="M6.6 10.8a15.1 15.1 0 0 0 6.6 6.6l2.2-2.2a1 1 0 0 1 1-.25 11.4 11.4 0 0 0 3.6.57 1 1 0 0 1 1 1V20a1 1 0 0 1-1 1A17 17 0 0 1 3 4a1 1 0 0 1 1-1h3.5a1 1 0 0 1 1 1c0 1.25.2 2.45.57 3.57a1 1 0 0 1-.25 1z" fill="var(--ink)"/>
        </svg>
        913-555-0147
      </li>
      <li>
        <svg class="contact-icon" viewBox="0 0 24 24" aria-hidden="true"><circle cx="12" cy="12" r="11" fill="var(--ink)"/></svg>
        Rosalind Thorpe Gardens
      </li>
      <li>
        <svg class="contact-icon" viewBox="0 0 24 24" aria-hidden="true"><circle cx="12" cy="12" r="11" fill="var(--ink)"/></svg>
        @RosalindThorpeGardens
      </li>
      <li>
        <svg class="contact-icon" viewBox="0 0 24 24" aria-hidden="true">
          <circle cx="12" cy="12" r="10" fill="none" stroke="var(--ink)" stroke-width="2.4"/>
          <ellipse cx="12" cy="12" rx="4.5" ry="10" fill="none" stroke="var(--ink)" stroke-width="2"/>
          <path d="M2 12h20" stroke="var(--ink)" stroke-width="2"/>
        </svg>
        www.RosalindThorpeGardens.example
      </li>
    </ul>
  </section>

  <section class="card card-back">
    <div class="back-ring">Rosalind<br>Thorpe<br>Gardens</div>
  </section>
</body>
</html>
```